Business Card Design

The Kestrel Lodge Inn is the most centrally located motel in Grafton.
We are the only family owned motel in Grafton.
Our colour scheme is blue, whiteand black.

I have uploaded a photo of our new rooms and the logo for you to use Thanks. Looking good

Industry/Entity Type

Motel

Contact Information for Business Card

The Kestrel Lodge Inn
Gareth & Lorna Pelling
Owner/Operators
14-16 Wexbury Lane, Grafton NSW 2460
Ph: 02 6617 3904
Email: thekestrellodgeinn@mailvista.example
reception@kestrellodgeinn.example.au
www.kestrellodgeinn.example.au

Colors
0392cd
0455a3

```html
<!DOCTYPE html>
<html lang="en">
<head>
<meta charset="utf-8">
<title>The Kestrel Lodge Inn — Business Card</title>
<link href="https://fonts.googleapis.com/css2?family=Exo+2:wght@400;500;700&display=swap" rel="stylesheet">
<style>
  :root {
    --navy: #0455a3;
    --sky: #0392cd;
    --pale: #8cc4ee;
    --white: #ffffff;
    --ink: #1b2a44;
    --stage: #d9dadb;
  }
  * { box-sizing: border-box; margin: 0; padding: 0; }
  html, body { width: 1200px; height: 949px; overflow: hidden; }
  body {
    background: var(--stage);
    font-family: "Exo 2", Arial, sans-serif;
    position: relative;
  }
  .card {
    position: absolute;
    left: 250px;
    width: 700px;
    height: 400px;
    background: var(--white);
    border-radius: 22px;
    overflow: hidden;
    box-shadow: 0 10px 30px rgba(0,0,0,0.18);
  }
  .card--front { top: 50px; }
  .card--back { top: 500px; }

  .brand { display: flex; align-items: center; gap: 14px; }
  .brand__dot { width: 34px; height: 34px; border-radius: 50%; background: var(--sky); flex: none; }
  .brand__name { font-weight: 700; font-size: 34px; color: var(--navy); letter-spacing: 0.5px; white-space: nowrap; }

  .front__head { position: absolute; left: 50px; top: 28px; }
  .front__person {
    position: absolute; left: 50px; top: 104px;
    display: flex; align-items: center; gap: 10px;
    font-size: 19px; color: var(--ink); letter-spacing: 1px; white-space: nowrap;
  }
  .front__person svg { width: 16px; height: 16px; fill: var(--navy); }
  .front__role { margin-left: 30px; letter-spacing: 0.5px; }
  .front__contact {
    position: absolute; left: 0; top: 150px; width: 100%; height: 250px;
    background: var(--navy);
  }
  .front__strip {
    position: absolute; left: 0; bottom: 0; width: 60px; height: 190px;
    background: var(--pale);
  }
  .contact-row {
    position: absolute; left: 60px; right: 0; height: 62.5px;
    display: flex; align-items: center; gap: 24px; padding-left: 30px;
    color: var(--white); font-size: 20px; letter-spacing: 0.6px;
    line-height: 1.2; white-space: nowrap;
    border-bottom: 1px solid rgba(255,255,255,0.55);
  }
  .contact-row:last-child { border-bottom: none; }
  .contact-row svg { width: 24px; height: 24px; flex: none; fill: var(--white); }
  .contact-row--stacked { font-size: 17px; }
  .row-1 { top: 0; } .row-2 { top: 62.5px; } .row-3 { top: 125px; } .row-4 { top: 187.5px; }

  .back__brand { position: absolute; left: 0; right: 0; top: 160px; display: flex; justify-content: center; }
  .back__band {
    position: absolute; left: 0; bottom: 0; width: 100%; height: 44px;
    background: var(--navy);
    display: flex; justify-content: flex-end; align-items: center; gap: 16px;
    padding-right: 34px;
  }
  .back__social { width: 18px; height: 18px; border-radius: 50%; background: var(--white); }
</style>
</head>
<body>

<section class="card card--front" aria-label="Business card front">
  <div class="front__head brand">
    <span class="brand__dot"></span>
    <span class="brand__name">The Kestrel Lodge Inn</span>
  </div>
  <div class="front__person">
    <svg viewBox="0 0 16 16" aria-hidden="true"><circle cx="8" cy="4.5" r="3.5"/><path d="M1 16c0-4 3-6.5 7-6.5s7 2.5 7 6.5z"/></svg>
    <span>GARETH &amp; LORNA PELLING</span>
    <span class="front__role">Owner/Operators</span>
  </div>

  <div class="front__contact">
    <div class="front__strip"></div>
    <div class="contact-row row-1">
      <svg viewBox="0 0 24 24" aria-hidden="true"><path d="M6.6 10.8a15.1 15.1 0 0 0 6.6 6.6l2.2-2.2c.3-.3.7-.4 1-.2 1.1.4 2.3.6 3.6.6.6 0 1 .4 1 1V20c0 .6-.4 1-1 1A17 17 0 0 1 3 4c0-.6.4-1 1-1h3.5c.6 0 1 .4 1 1 0 1.3.2 2.5.6 3.6.1.3 0 .7-.2 1z"/></svg>
      <span>Ph: 02 6617 3904</span>
    </div>
    <div class="contact-row row-2 contact-row--stacked">
      <svg viewBox="0 0 24 24" aria-hidden="true"><path d="M2 5h20v14H2z M3.5 6.5v.4L12 13l8.5-6.1v-.4z" fill-rule="evenodd"/></svg>
      <span>thekestrellodgeinn@mailvista.example<br>reception@kestrellodgeinn.example.au</span>
    </div>
    <div class="contact-row row-3">
      <svg viewBox="0 0 24 24" aria-hidden="true"><path fill-rule="evenodd" d="M12 2a10 10 0 1 1 0 20 10 10 0 0 1 0-20zm-1 2.1A8 8 0 0 0 4.1 11H8c.1-2.6.9-5 3-6.9zm2 0c2.1 1.9 2.9 4.3 3 6.9h3.9A8 8 0 0 0 13 4.1zM10 11h4c-.1-2.3-.8-4.2-2-5.6-1.2 1.4-1.9 3.3-2 5.6zm-5.9 2A8 8 0 0 0 11 19.9c-2.1-1.9-2.9-4.3-3-6.9zm5.9 0c.1 2.3.8 4.2 2 5.6 1.2-1.4 1.9-3.3 2-5.6zm6 0c-.1 2.6-.9 5-3 6.9a8 8 0 0 0 6.9-6.9z"/></svg>
      <span>www.kestrellodgeinn.example.au</span>
    </div>
    <div class="contact-row row-4 contact-row--stacked">
      <svg viewBox="0 0 24 24" aria-hidden="true"><path fill-rule="evenodd" d="M12 2a7 7 0 0 1 7 7c0 5-7 13-7 13S5 14 5 9a7 7 0 0 1 7-7zm0 4a3 3 0 1 0 0 6 3 3 0 0 0 0-6z"/></svg>
      <span>14-16 Wexbury Lane<br>Grafton NSW 2460</span>
    </div>
  </div>
</section>

<section class="card card--back" aria-label="Business card back">
  <div class="back__brand brand">
    <span class="brand__dot"></span>
    <span class="brand__name">The Kestrel Lodge Inn</span>
  </div>
  <div class="back__band">
    <span class="back__social"></span>
    <span class="back__social"></span>
    <span class="back__social"></span>
  </div>
</section>

</body>
</html>
```